OpenHarbor Yoga Website Design

Business Logo - attached
5 pages being:
Home
About
Classes
Blog
Contact

Would like Scrolling webpage and yoga symbols to be used.

Must have's being:
Easy to navigate, Text needs to be able to be edited/updated, Enquire Now Links, More Information Links, be a secure site, SEO,

Please refer to attached document for the information for the body of the website.

Target Market(s)

Educators, Community Service, Health and Wellbeing, Mental Health

Industry/Entity Type

Yoga

Coding

Coded - Design and coding required

Number of Pages Required

5+ page

Font styles to use
Other font styles liked:
• Bella Bold BC

Colors
0094D4
00A9DD
6FCCEA
C7EBF8
E9F6FB
6B429C
8869AF
B7A5CE
E3DAEB
F3F0F8

Requirements
Must have
• Easy to navigate, Text needs to be able to be edited/updated, Enquire Now Links, More Information Links, be a secure site, SEO,
Nice to have
• Scrolling webpage, yoga symbols

```html
<!DOCTYPE html>
<html lang="en">
<head>
<meta charset="utf-8">
<title>OpenHarbor Yoga – Website Pages</title>
<link href="https://fonts.googleapis.com/css2?family=Open+Sans:wght@300;400;600;700&family=Yellowtail&display=swap" rel="stylesheet">
<style>
:root{
  --board:#ae8fe0;
  --deep:#4a2c92;
  --purple:#6b429c;
  --violet:#7a4fc0;
  --teal:#22b8d2;
  --sky:#26b5d0;
  --foot:#54448f;
  --ink:#3f2488;
  --text:#5a5a66;
  --page:#f5f5f7;
  --grey:#eeeef1;
  --blush:#f8f3f8;
  --white:#ffffff;
}
*{box-sizing:border-box;margin:0;padding:0}
html,body{width:1124px;height:1200px;overflow:hidden;background:var(--board)}
body{font-family:"Open Sans",Arial,sans-serif}
.board{position:relative;width:1124px;height:1200px;overflow:hidden;background:var(--board)}
.board-title{position:absolute;transform:translateX(-50%);white-space:nowrap;color:#f4efff;font-weight:300;font-size:10px}
.note{position:absolute;color:#f4efff;font-size:5px;line-height:5.2px;text-align:center;width:44px}
.arrows{position:absolute;left:0;top:0}

.page{position:absolute;width:172px;background:var(--page);overflow:hidden}
.page > *{position:absolute}
.topbar{left:0;top:0;width:172px;height:7px;background:linear-gradient(90deg,#3f2a8c,#5a3ca8 40%,#24b4d0);color:#fff;font-size:2.2px;display:flex;align-items:center;justify-content:flex-end;padding-right:18px;gap:3px}
.topbar b{font-weight:600}
.navbar{left:0;top:7px;width:172px;height:15px;background:var(--white);display:flex;align-items:center}
.nav-brand{position:absolute;left:8px;top:1.5px;display:flex;align-items:center;gap:1.5px}
.nav-brand i{display:block;width:12px;height:12px;border-radius:50%;border:.5px solid #c9b8e6}
.menu{position:absolute;left:56px;top:4.5px;display:flex;gap:5.5px;font-size:2.4px;color:#333}
.menu .on{border-bottom:.6px solid var(--deep);padding-bottom:1px}
.pill{position:absolute;left:133px;top:4.2px;width:20px;height:6px;border-radius:3px;background:linear-gradient(90deg,#6a3fb6,#22b8d2);color:#fff;font-size:2.2px;display:flex;align-items:center;justify-content:center;font-weight:600}
.hero{left:0;top:22px;width:172px;height:67px;background:linear-gradient(180deg,#4a2c92 0%,#6a45b6 28%,#4a8fd2 65%,#1fc2d8 100%);display:flex;flex-direction:column;align-items:center;justify-content:center;gap:4px}
.hero-mark{width:22px;height:22px;border-radius:50%;border:1px solid rgba(255,255,255,.8)}
.hero-name{color:#fff;font-size:7px;font-weight:300;letter-spacing:.4px}

.script{font-family:"Yellowtail",cursive;font-weight:400;color:var(--ink);white-space:nowrap}
.class-head{font-size:6px;line-height:6.5px;width:78px;white-space:normal}
.p{font-size:2.4px;line-height:3.2px;color:var(--text)}
.c{text-align:center}
.list{list-style:none;font-size:2.3px;line-height:3.3px;color:var(--text)}
.list li::before{content:"";display:inline-block;width:2px;height:1.6px;margin-right:1.5px;background:var(--purple);clip-path:polygon(50% 0,100% 100%,0 100%)}
.btn{display:inline-flex;align-items:center;justify-content:center;height:5.5px;padding:0 4px;border-radius:3px;background:linear-gradient(90deg,#6a3fb6,#22b8d2);color:#fff;font-size:2.2px;font-weight:600;white-space:nowrap}
.frame{border:1px solid var(--purple)}
.band{left:0;width:172px}

.card{background:var(--white);box-shadow:0 0 2px rgba(0,0,0,.08)}
.card > *{position:absolute}
.side-title{font-family:"Yellowtail",cursive;font-weight:400;color:var(--ink);font-size:6px}
.side-item{display:flex;gap:2px;width:44px}
.side-item i{display:block;width:11px;height:9px;flex:none;background:linear-gradient(135deg,#7d6a8a,#c9b2a0)}
.side-item b{font-size:1.8px;line-height:2.3px;color:var(--ink);font-weight:700}
.side-item em{display:block;font-style:normal;color:var(--teal);font-weight:400}
.field{background:var(--white);border:.4px solid #d8d8e0;font-size:1.8px;color:#999;padding:.6px 1px}

.footer{left:0;width:172px;background:var(--foot);color:#fff}
.footer > *{position:absolute}
.foot-h{font-family:"Yellowtail",cursive;font-weight:400;font-size:5.5px}
.foot-l{font-size:1.9px;line-height:2.9px}
.foot-mark{left:79px;top:11px;display:flex;flex-direction:column;align-items:center;gap:1.5px;width:16px}
.foot-mark i{display:block;width:10px;height:10px;border-radius:50%;border:.5px solid rgba(255,255,255,.8)}
.foot-mark span{font-size:1.8px;white-space:nowrap}
.copy{left:0;width:172px;text-align:center;font-size:1.9px}
</style>
</head>
<body>
<main class="board">

  <p class="board-title" style="left:256px;top:129px">Home Page</p>
  <p class="board-title" style="left:463px;top:129px">Classes Page Sample 2</p>
  <p class="board-title" style="left:670px;top:129px">Blog Page Sample 2</p>
  <p class="board-title" style="left:877px;top:129px">Single Blog Page Sample 2</p>
  <p class="board-title" style="left:675px;top:702px">Contact Us Page</p>
  <p class="board-title" style="left:248px;top:763px">About Page</p>

  <svg class="arrows" width="1124" height="1200" viewBox="0 0 1124 1200" aria-hidden="true">
    <polyline points="492,755 564,755 564,862 580,862" fill="none" stroke="#222" stroke-width=".6"/>
    <polygon points="582,862 578,860.3 578,863.7" fill="#222"/>
    <line x1="670" y1="887" x2="772" y2="887" stroke="#222" stroke-width=".6"/>
    <polygon points="775,887 771,885.3 771,888.7" fill="#222"/>
  </svg>
  <p class="note" style="left:552px;top:874px">Enquire &nbsp;links go to the contact form</p>
  <p class="note" style="left:773px;top:881px">Subscribe to Newsletter Option</p>

  <!-- HOME -->
  <section class="page" style="left:170px;top:153px;height:578px">
    <div class="topbar"><span>info@openharboryoga.com.au</span><b>Call Us: 0400 118 236</b></div>
    <nav class="navbar"><div class="nav-brand"><i></i></div>
      <div class="menu"><span class="on">Home</span><span>About</span><span>Classes</span><span>Blog</span><span>Contact</span></div>
      <span class="pill">Enquire Now</span></nav>
    <header class="hero" style="height:80px"><i class="hero-mark"></i><span class="hero-name">OpenHarbor Yoga</span></header>
    <div style="left:0;top:102px;width:172px;height:101px;background:var(--white)"></div>
    <h2 class="script" style="left:0;width:172px;text-align:center;top:114px;font-size:9px">Welcome to OpenHarbor Yoga...</h2>
    <div style="left:13px;top:139px;width:59px;height:54px;border:.5px solid #ccc"></div>
    <div role="img" aria-label="Woman meditating cross-legged on a yoga mat" style="left:18px;top:134px;width:59px;height:54px;background:linear-gradient(135deg,#c7b8a8,#8d7a6e 60%,#54505a)"></div>
    <div class="p" style="left:81px;top:133px;width:74px">OpenHarbor Yoga believe that you are never too young to benefit from and fall in love with yoga. My aim is to empower kids and teens to thrive by teaching life skills in yoga, mindfulness and breathing techniques to deal with daily challenges and big emotions.<br><br>OpenHarbor Yoga gives kids an opportunity to enjoy and experience yoga for themselves and primarily focuses on programs for schools, pre-schools and early learning centres, private classes, sporting clubs, martial arts schools, scout groups and therapy centres.</div>
    <span class="btn" style="left:81px;top:185px">More Information</span>
    <div class="band" style="top:203px;height:57px;background:var(--sky)"></div>
    <h2 class="script" style="left:0;width:172px;text-align:center;top:213px;font-size:8px;color:#fff">Benefits of Yoga...</h2>
    <p class="p c" style="left:36px;top:228px;width:100px;color:#fff">The benefits of yoga can last a lifetime. It is my aim and passion to introduce yoga to kids of all ages and backgrounds so that they can not only experience the benefits but fall in love with the practice.</p>
    <p class="script" style="left:0;width:172px;text-align:center;top:242px;font-size:6.5px;color:#fff">Yoga benefits include:</p>
    <h3 class="script" style="left:18px;top:274px;font-size:7px">Healthy Bodies</h3>
    <ul class="list" style="left:18px;top:284px;width:66px">
      <li>Develops strong, flexible and healthy bodies</li><li>Promotes spinal alignment and good posture</li><li>Builds energy and stamina</li><li>Improves internal physical function</li><li>Helps breathing and lung capacity</li><li>Teaches the enjoyment of movement</li><li>Works the 'whole' body</li></ul>
    <div class="frame" style="left:87px;top:281px;width:71px;height:47px"></div>
    <div role="img" aria-label="Child in a downward dog pose at home" style="left:84px;top:278px;width:71px;height:47px;background:linear-gradient(135deg,#d8d4cc,#a49c92 60%,#6b8da8)"></div>
    <div class="frame" style="left:10px;top:346px;width:70px;height:47px"></div>
    <div role="img" aria-label="Group of girls doing yoga on mats" style="left:13px;top:343px;width:70px;height:46px;background:linear-gradient(135deg,#e0c7b7,#d99a8c 50%,#6fb3d6)"></div>
    <h3 class="script" style="left:94px;top:345px;font-size:7px">Healthy Minds</h3>
    <ul class="list" style="left:94px;top:355px;width:70px">
      <li>Cultivates confidence and self-esteem</li><li>Develops concentration and attention</li><li>Clears the mind for better decision making</li><li>Helps relax and sleep better</li><li>Calms the nervous system</li><li>Learns to cope with stressful situations</li><li>Balances emotions</li></ul>
    <h3 class="script" style="left:18px;top:408px;font-size:7px">Healthy Spirits</h3>
    <ul class="list" style="left:18px;top:418px;width:64px">
      <li>Fosters creativity and imagination</li><li>Cultivates kindness to themselves</li><li>Cultivates respect for self and others</li><li>Builds balance and inner quiet</li><li>Builds inner strength and resilience</li><li>Teaches self awareness</li><li>Focuses on positive self-talk</li></ul>
    <div style="left:84px;top:415px;width:71px;height:47px;border:1px solid var(--teal)"></div>
    <div role="img" aria-label="Class of adults stretching on yoga mats" style="left:81px;top:412px;width:71px;height:47px;background:linear-gradient(135deg,#d9d2cc,#9b8a82 55%,#5b4e4c)"></div>
    <p class="p c" style="left:26px;top:479px;width:120px">OpenHarbor Yoga combines all the benefits of traditional yoga and a lot of fun! We play games and practice engaging flows which get our bodies moving, then we take a quiet moment to be still and calm as we focus on our breathing.<br><br>OpenHarbor Yoga Kids will learn that relaxation is just as important as moving their bodies, and the exercises they learn in class can easily be repeated at any time.</p>
    <footer class="footer" style="top:521px;height:57px">
      <h4 class="foot-h" style="left:19px;top:10px">Contact Us</h4>
      <p class="foot-l" style="left:19px;top:19px">Contact: Dana Whitfield<br>Phone: 0400 118 236<br>Email: info@openharboryoga.com.au<br>Location: Lakeview, Victoria Australia 3999</p>
      <div class="foot-mark"><i></i><span>OpenHarbor Yoga</span></div>
      <h4 class="foot-h" style="left:106px;top:10px">Connect With Us</h4>
      <p class="foot-l" style="left:106px;top:19px">Facebook: OpenHarbor Yoga<br>Instagram: openharboryogakids<br><br>ABN: 11 222 333 444</p>
      <p class="copy" style="top:49px">Copyright 2023 OpenHarbor Yoga</p>
    </footer>
  </section>

  <!-- CLASSES -->
  <section class="page" style="left:377px;top:153px;height:947px">
    <div class="topbar"><span>info@openharboryoga.com.au</span><b>Call Us: 0400 118 236</b></div>
    <nav class="navbar"><div class="nav-brand"><i></i></div>
      <div class="menu"><span>Home</span><span>About</span><span class="on">Classes</span><span>Blog</span><span>Contact</span></div>
      <span class="pill">Enquire Now</span></nav>
    <header class="hero"><i class="hero-mark"></i><span class="hero-name">OpenHarbor Yoga</span></header>
    <div style="left:0;top:89px;width:172px;height:151px;background:var(--white)"></div>
    <h2 class="script" style="left:0;width:172px;text-align:center;top:97px;font-size:9px">OpenHarbor Kids Yoga Classes...</h2>
    <p class="p c" style="left:36px;top:110px;width:100px">Does your child or teen get anxious? Would they benefit from activities that help to build resilience, without competition or pressure?</p>
    <p class="script" style="left:18px;top:126px;font-size:4.5px;color:var(--purple);white-space:normal;width:62px;line-height:4.2px">OpenHarbor Yoga offers a range of options of classes for kids and teens:</p>
    <ul class="list" style="left:18px;top:136px;width:66px"><li>after school classes (day and location)</li><li>day care/ early learning (age 2 - preschool)</li><li>school (as part of the curriculum)</li><li>private sessions (in person at location)</li></ul>
    <p class="script" style="left:18px;top:153px;font-size:4.5px;color:var(--purple);white-space:normal;width:62px;line-height:4.2px">Classes are a perfect blend of fun + calm and include:</p>
    <ul class="list" style="left:18px;top:163px;width:66px"><li>mindful movements</li><li>stretches to improve flexibility</li><li>exercises to help build strength and posture</li><li>fun group activities and team games</li><li>calm breathing techniques</li><li>mindfulness activities</li><li>guided relaxation to reduce anxiety</li></ul>
    <p class="p" style="left:18px;top:200px;width:66px">Classes are tailored to meet the unique needs of the group to be age appropriate and suitable for their capability.</p>
    <div style="left:84px;top:136px;width:10px;height:10px;background:var(--purple)"></div>
    <div role="img" aria-label="Collage of children practising yoga poses" style="left:87px;top:139px;width:66px;height:32px;background:linear-gradient(135deg,#cfc7e0,#9a90b0 50%,#e6e4ee)"></div>
    <div role="img" aria-label="Children stretching together in a class" style="left:87px;top:173px;width:66px;height:44px;background:linear-gradient(135deg,#9fc9e8,#d8b8a8 50%,#5a9fd0)"></div>
    <div style="left:140px;top:214px;width:16px;height:2px;background:var(--purple)"></div>
    <div class="band" style="top:240px;height:163px;background:var(--grey)"></div>
    <div role="img" aria-label="Colourful magnetic number toys" style="left:18px;top:254px;width:70px;height:45px;background:linear-gradient(120deg,#e8453c,#f2b230 40%,#3aa85a 70%,#4a6ec8)"></div>
    <h3 class="script class-head" style="left:91px;top:252px">Yoga in Early Learning ...</h3>
    <p class="script" style="left:91px;top:261px;font-size:4px;width:66px;white-space:normal;line-height:4.2px;color:var(--text)">Offer OpenHarbor Yoga at your childcare centre or kindergarten!</p>
    <p class="p" style="left:91px;top:272px;width:66px">Give little ones a way to let out their energy in a healthy and mindful environment. OpenHarbor Yoga's experienced kids yoga teacher teach children to have fun with yoga, build strength, focus, balance and coordination in a kind and nurturing way.<br><br>Yoga sessions can be tailored for the different ages of children, group size, curriculum strand or themes in the centre.</p>
    <ul class="list" style="left:91px;top:314px"><li>15 min classes with ages 2-3</li><li>20 min class with ages 3-4</li><li>30 min class with ages 4-5</li></ul>
    <h3 class="script" style="left:18px;top:328px;font-size:7px">Yoga in Schools...</h3>
    <p class="script" style="left:18px;top:338px;font-size:4px;color:var(--text)">Offer OpenHarbor Yoga at your school!</p>
    <p class="p" style="left:18px;top:346px;width:66px">Classes are tailored by the age of students, group size, curriculum strand or made relevant to a subject, term program or one-off class for both primary and high schools. We bring yoga to you, with options including after school yoga club, yoga as a PE unit, or yoga in health class.<br><br>Experienced kids and teens yoga teacher that engage kids with thoughtful yoga classes that develop strength, focus, confidence and more. Online classes are also available.</p>
    <div role="img" aria-label="Books, pencils and an apple in front of a chalkboard" style="left:89px;top:342px;width:63px;height:39px;background:linear-gradient(135deg,#3a3a3a,#5a5a4e 55%,#c84a2c)"></div>
    <div role="img" aria-label="Girl sitting in a meditation pose" style="left:17px;top:419px;width:67px;height:69px;background:linear-gradient(135deg,#ece9e6,#b9aea6 55%,#7c7270)"></div>
    <h3 class="script class-head" style="left:90px;top:417px">Yoga for Tweens (aged 7-11)...</h3>
    <p class="p" style="left:90px;top:427px;width:66px">An interactive 60-minute class for children aged 7-11 to enjoy yoga poses, games, partner yoga and learning life skills in a fun way. Each class ends with quiet time to breathe and relax.</p>
    <p class="p" style="left:90px;top:447px;width:30px"><b>When:</b><br>Day &amp; Time<br>Term: Aug 20 - Sept 7</p>
    <p class="p" style="left:123px;top:447px;width:30px"><b>Where:</b><br>TBC</p>
    <p class="p" style="left:90px;top:461px;width:66px"><b>Cost:</b><br>$55 4 class pass<br>$110 term pass<br>$170 term pass for 2 siblings<br>No credits for missed classes</p>
    <span class="btn" style="left:90px;top:484px">Enquire Now</span>
    <div role="img" aria-label="Teen girls in a yoga class doing downward dog" style="left:17px;top:504px;width:67px;height:68px;background:linear-gradient(135deg,#eceae8,#c79aa0 55%,#8a7a86)"></div>
    <h3 class="script class-head" style="left:90px;top:501px">Yoga for Teen Girls...</h3>
    <p class="p" style="left:90px;top:511px;width:66px">A beautiful class for teen girls to learn life skills and build self-confidence through yoga poses and empowering affirmations and partner yoga. Each class ends with quiet time to breathe and relax.<br><br>If your daughter is not yet a teen, but is in high school, she can join.</p>
    <p class="p" style="left:90px;top:545px;width:30px"><b>When:</b><br>Thursday, 5-6pm<br>Term 3: July 20 - Sept 7</p>
    <p class="p" style="left:123px;top:545px;width:30px"><b>Where:</b><br>TBC</p>
    <p class="p" style="left:90px;top:559px;width:66px"><b>Cost:</b><br>$60 4 class pass<br>$120 term pass<br>$180 term pass for 2 siblings<br>No credits for missed classes</p>
    <span class="btn" style="left:90px;top:582px">Enquire Now</span>
    <div class="band" style="top:602px;height:68px;background:#5a469a"></div>
    <h2 class="script" style="left:0;width:172px;text-align:center;top:609px;font-size:8px;color:#fff">Private Sessions...</h2>
    <p class="p c" style="left:30px;top:621px;width:112px;color:#fff">If a group class is not suitable for your child, or if they would benefit from an individualised program to suit their needs, then you can consider a private lesson.<br>As a Kids Yoga Teacher, I have a Working with Children's Check card, first aid certificate, insurance, and relevant qualifications.<br><br>One on one, private sessions are the most effective way to ensure the student receives exactly what is right for them in the moment.</p>
    <span class="btn" style="left:74px;top:655px;background:var(--violet);border:.4px solid #fff">Enquire Now</span>
    <div class="band" style="top:670px;height:64px;background:var(--blush)"></div>
    <div role="img" aria-label="Child following an online yoga class on a laptop" style="left:37px;top:679px;width:44px;height:44px;border-radius:50%;background:linear-gradient(135deg,#3f6fb8,#9ab8d8 50%,#6fc0e0)"></div>
    <h3 class="script" style="left:91px;top:679px;font-size:7px">Kids Yoga Online</h3>
    <p class="p" style="left:91px;top:689px;width:56px">"Online" is the new world we live in... So, if face to face sessions with me aren't possible, check out these options.</p>
    <div class="band" style="top:734px;height:156px;background:var(--white)"></div>
    <h3 class="script" style="left:18px;top:747px;font-size:4.8px;width:64px">Online private sessions for kids</h3>
    <p class="p" style="left:18px;top:755px;width:62px">Online private sessions on zoom are designed for kids who physically cannot make it to a yoga class, either due to distance, anxiety, or medical reasons. I will tailor the activities and duration (30-60 mins) to suit their individual needs.</p>
    <p class="p" style="left:18px;top:780px;width:62px;color:#222;font-weight:700">Yes! I want my child to learn calm tools in a tailored, online private session</p>
    <span class="btn" style="left:18px;top:788px">Enquire Now</span>
    <div role="img" aria-label="Mother and child doing a yoga pose at home" style="left:84px;top:746px;width:69px;height:45px;background:linear-gradient(135deg,#dbe6ee,#c4a48e 55%,#8ec2d4)"></div>
    <div role="img" aria-label="Children doing a tree pose outdoors on grass" style="left:16px;top:806px;width:69px;height:66px;background:linear-gradient(180deg,#d9c9b0,#c98e7c 45%,#6f9a52)"></div>
    <h3 class="script" style="left:91px;top:804px;font-size:4.8px;width:64px">Online sessions for schools</h3>
    <p class="p" style="left:91px;top:812px;width:62px">If you want to schedule in a little chill out time between lessons, or at the end of a structured day of learning, I will teach a class that is tailored to your group's age and needs. They don't even need to look at the screen the whole time!<br><br>Options for:<br>- Preschool &amp; Prep<br>- Primary School<br>- High School</p>
    <p class="p" style="left:91px;top:857px;width:62px;color:#222;font-weight:700">Yes! Our kids would benefit from some chill out time</p>
    <span class="btn" style="left:91px;top:868px;background:var(--violet)">Enquire Now</span>
    <footer class="footer" style="top:890px;height:57px">
      <h4 class="foot-h" style="left:19px;top:10px">Contact Us</h4>
      <p class="foot-l" style="left:19px;top:19px">Contact: Dana Whitfield<br>Phone: 0400 118 236<br>Email: info@openharboryoga.com.au<br>Location: Lakeview, Victoria Australia 3999</p>
      <div class="foot-mark"><i></i><span>OpenHarbor Yoga</span></div>
      <h4 class="foot-h" style="left:106px;top:10px">Connect With Us</h4>
      <p class="foot-l" style="left:106px;top:19px">Facebook: OpenHarbor Yoga<br>Instagram: openharboryogakids<br><br>ABN: 11 222 333 444</p>
      <p class="copy" style="top:49px">Copyright 2023 OpenHarbor Yoga</p>
    </footer>
  </section>

  <!-- BLOG -->
  <section class="page" style="left:584px;top:153px;height:532px">
    <div class="topbar"><span>info@openharboryoga.com.au</span><b>Call Us: 0400 118 236</b></div>
    <nav class="navbar"><div class="nav-brand"><i></i></div>
      <div class="menu"><span>Home</span><span>About</span><span>Classes</span><span class="on">Blog</span><span>Contact</span></div>
      <span class="pill">Enquire Now</span></nav>
    <header class="hero"><i class="hero-mark"></i><span class="hero-name">OpenHarbor Yoga</span></header>
    <h2 class="script" style="left:15px;top:101px;font-size:9px">Latest Blog Posts</h2>

    <article class="card" style="left:16px;top:117px;width:86px;height:61px">
      <div role="img" aria-label="Yoga class photo" style="left:4px;top:6px;width:24px;height:22px;background:linear-gradient(135deg,#8fb0d8,#d08a9a 50%,#4a6a9a)"></div>
      <h3 style="left:31px;top:7px;width:50px;font-size:2.6px;line-height:3px;color:var(--ink)">Lorem ipsum dolor sit ame consectetur adipiscinlore elised do eiusmod</h3>
      <p class="p" style="left:31px;top:17px;font-size:1.8px;color:var(--teal)">Aug 08, 2023 · 2 · 947</p>
      <p class="p" style="left:4px;top:33px;width:78px;font-size:1.8px;line-height:2.4px">Lorem ipsum dolor sit amet, consectetur adipiscing elit, sed do eiusmod tempor incididunt ut labore et dolore magna aliqua. Quis ipsum suspendisse ultrices gravida commodo viverra maecenas.</p>
      <i style="left:4px;top:47px;width:8px;height:8px;border-radius:50%;background:#ccc"></i>
      <p class="p" style="left:14px;top:49px;font-size:1.8px;color:var(--ink)">Added by<br><b>Dana Whitfield</b></p>
      <span class="btn" style="left:59px;top:49px;height:4.5px;font-size:1.7px;padding:0 2px;background:var(--teal)">Continue Reading</span>
    </article>
    <article class="card" style="left:16px;top:184px;width:86px;height:61px">
      <div role="img" aria-label="Child in a yoga pose" style="left:4px;top:6px;width:24px;height:22px;background:linear-gradient(135deg,#e8e6e2,#a89e98 60%,#6a5e5a)"></div>
      <h3 style="left:31px;top:7px;width:50px;font-size:2.6px;line-height:3px;color:var(--ink)">Lorem ipsum dolor sit ame consectetur adipiscinlore elised do eiusmod</h3>
      <p class="p" style="left:31px;top:17px;font-size:1.8px;color:var(--teal)">Aug 08, 2023 · 2 · 947</p>
      <p class="p" style="left:4px;top:33px;width:78px;font-size:1.8px;line-height:2.4px">Lorem ipsum dolor sit amet, consectetur adipiscing elit, sed do eiusmod tempor incididunt ut labore et dolore magna aliqua. Quis ipsum suspendisse ultrices gravida commodo viverra maecenas.</p>
      <i style="left:4px;top:47px;width:8px;height:8px;border-radius:50%;background:#ccc"></i>
      <p class="p" style="left:14px;top:49px;font-size:1.8px;color:var(--ink)">Added by<br><b>Dana Whitfield</b></p>
      <span class="btn" style="left:59px;top:49px;height:4.5px;font-size:1.7px;padding:0 2px;background:var(--teal)">Continue Reading</span>
    </article>
    <article class="card" style="left:16px;top:250px;width:86px;height:61px">
      <div role="img" aria-label="Adults stretching on mats" style="left:4px;top:6px;width:24px;height:22px;background:linear-gradient(135deg,#d8d0c8,#8a7c70 60%,#5a524c)"></div>
      <h3 style="left:31px;top:7px;width:50px;font-size:2.6px;line-height:3px;color:var(--ink)">Lorem ipsum dolor sit ame consectetur adipiscinlore elised do eiusmod</h3>
      <p class="p" style="left:31px;top:17px;font-size:1.8px;color:var(--teal)">Aug 08, 2023 · 2 · 947</p>
      <p class="p" style="left:4px;top:33px;width:78px;font-size:1.8px;line-height:2.4px">Lorem ipsum dolor sit amet, consectetur adipiscing elit, sed do eiusmod tempor incididunt ut labore et dolore magna aliqua. Quis ipsum suspendisse ultrices gravida commodo viverra maecenas.</p>
      <i style="left:4px;top:47px;width:8px;height:8px;border-radius:50%;background:#ccc"></i>
      <p class="p" style="left:14px;top:49px;font-size:1.8px;color:var(--ink)">Added by<br><b>Dana Whitfield</b></p>
      <span class="btn" style="left:59px;top:49px;height:4.5px;font-size:1.7px;padding:0 2px;background:var(--teal)">Continue Reading</span>
    </article>
    <article class="card" style="left:16px;top:317px;width:86px;height:61px">
      <div role="img" aria-label="Girl in a joyful yoga pose" style="left:4px;top:6px;width:24px;height:22px;background:linear-gradient(135deg,#f0d8d0,#d86a6a 50%,#e8c0b0)"></div>
      <h3 style="left:31px;top:7px;width:50px;font-size:2.6px;line-height:3px;color:var(--ink)">Lorem ipsum dolor sit ame consectetur adipiscinlore elised do eiusmod</h3>
      <p class="p" style="left:31px;top:17px;font-size:1.8px;color:var(--teal)">Aug 08, 2023 · 2 · 947</p>
      <p class="p" style="left:4px;top:33px;width:78px;font-size:1.8px;line-height:2.4px">Lorem ipsum dolor sit amet, consectetur adipiscing elit, sed do eiusmod tempor incididunt ut labore et dolore magna aliqua. Quis ipsum suspendisse ultrices gravida commodo viverra maecenas.</p>
      <i style="left:4px;top:47px;width:8px;height:8px;border-radius:50%;background:#ccc"></i>
      <p class="p" style="left:14px;top:49px;font-size:1.8px;color:var(--ink)">Added by<br><b>Dana Whitfield</b></p>
      <span class="btn" style="left:59px;top:49px;height:4.5px;font-size:1.7px;padding:0 2px;background:var(--teal)">Continue Reading</span>
    </article>
    <article class="card" style="left:16px;top:384px;width:86px;height:61px">
      <div role="img" aria-label="Children doing yoga outdoors" style="left:4px;top:6px;width:24px;height:22px;background:linear-gradient(135deg,#d8c0a0,#d07a6a 50%,#6f9a52)"></div>
      <h3 style="left:31px;top:7px;width:50px;font-size:2.6px;line-height:3px;color:var(--ink)">Lorem ipsum dolor sit ame consectetur adipiscinlore elised do eiusmod</h3>
      <p class="p" style="left:31px;top:17px;font-size:1.8px;color:var(--teal)">Aug 08, 2023 · 2 · 947</p>
      <p class="p" style="left:4px;top:33px;width:78px;font-size:1.8px;line-height:2.4px">Lorem ipsum dolor sit amet, consectetur adipiscing elit, sed do eiusmod tempor incididunt ut labore et dolore magna aliqua. Quis ipsum suspendisse ultrices gravida commodo viverra maecenas.</p>
      <i style="left:4px;top:47px;width:8px;height:8px;border-radius:50%;background:#ccc"></i>
      <p class="p" style="left:14px;top:49px;font-size:1.8px;color:var(--ink)">Added by<br><b>Dana Whitfield</b></p>
      <span class="btn" style="left:59px;top:49px;height:4.5px;font-size:1.7px;padding:0 2px;background:var(--teal)">Continue Reading</span>
    </article>

    <h4 class="side-title" style="left:112px;top:114px">Recent Posts</h4>
    <div class="side-item" style="left:113px;top:126px"><i></i><b>Lorem ipsum dolor sit amet, consectetur loremalilist<em>August 11, 2023</em></b></div>
    <div class="side-item" style="left:113px;top:142px"><i></i><b>Lorem ipsum dolor sit amet, consectetur loremalilist<em>August 11, 2023</em></b></div>
    <div class="side-item" style="left:113px;top:159px"><i></i><b>Lorem ipsum dolor sit amet, consectetur loremalilist<em>August 11, 2023</em></b></div>
    <div class="side-item" style="left:113px;top:175px"><i></i><b>Lorem ipsum dolor sit amet, consectetur loremalilist<em>August 11, 2023</em></b></div>
    <h4 class="side-title" style="left:113px;top:202px">Advertising</h4>
    <div role="img" aria-label="Advert photo of smiling children in a row" style="left:113px;top:215px;width:41px;height:36px;background:linear-gradient(135deg,#9ccbe8,#d9b0a0 50%,#6fa8d8)"></div>
    <div style="left:113px;top:251px;width:41px;height:21px;background:var(--purple);clip-path:polygon(0 15%,100% 0,100% 100%,0 100%)"></div>
    <p class="script" style="left:113px;top:257px;width:41px;text-align:center;white-space:normal;font-size:3px;line-height:3.2px;color:#fff">Lorem ipsum dolor sit amet consectetur adipiscing elit sed do eiusmod temp</p>
    <p class="p" style="left:68px;top:463px;font-size:2.4px;color:#333">Page 1 of 3</p>
    <span class="btn" style="left:88px;top:461px;background:var(--teal)">Next</span>
    <footer class="footer" style="top:479px;height:53px">
      <h4 class="foot-h" style="left:19px;top:8px">Contact Us</h4>
      <p class="foot-l" style="left:19px;top:17px">Contact: Dana Whitfield<br>Phone: 0400 118 236<br>Email: info@openharboryoga.com.au<br>Location: Lakeview, Victoria Australia 3999</p>
      <div class="foot-mark" style="top:9px"><i></i><span>OpenHarbor Yoga</span></div>
      <h4 class="foot-h" style="left:106px;top:8px">Connect With Us</h4>
      <p class="foot-l" style="left:106px;top:17px">Facebook: OpenHarbor Yoga<br>Instagram: openharboryogakids<br><br>ABN: 11 222 333 444</p>
      <p class="copy" style="top:45px">Copyright 2023 OpenHarbor Yoga</p>
    </footer>
  </section>

  <!-- SINGLE BLOG -->
  <section class="page" style="left:791px;top:153px;height:503px">
    <div class="topbar"><span>info@openharboryoga.com.au</span><b>Call Us: 0400 118 236</b></div>
    <nav class="navbar"><div class="nav-brand"><i></i></div>
      <div class="menu"><span>Home</span><span>About</span><span>Classes</span><span class="on">Blog</span><span>Contact</span></div>
      <span class="pill">Enquire Now</span></nav>
    <header class="hero"><i class="hero-mark"></i><span class="hero-name">OpenHarbor Yoga</span></header>
    <article class="card" style="left:13px;top:105px;width:94px;height:236px">
      <h2 style="left:8px;top:7px;width:80px;font-size:4px;line-height:4.8px;color:var(--ink)">Lorem ipsum dolor sit ametlol cons ectetur adipiscing elitlorem.</h2>
      <div role="img" aria-label="Group of people in athletic wear standing together" style="left:8px;top:20px;width:80px;height:48px;background:linear-gradient(180deg,#b8a89a,#8a7a70 50%,#d8cec6)"></div>
      <p class="p" style="left:8px;top:71px;font-size:1.9px;color:#333">Apr 30, 2023 · 1 min read · 2 · 947 · Admin</p>
      <p class="p" style="left:8px;top:76px;width:80px;font-size:1.8px;line-height:2.4px">Lorem ipsum dolor sit amet, consectetur adipiscing elit, sed do eiusmod tempor incididunt ut labore et dolore magna aliqua. Quis ipsum suspendisse ultrices gravida. Risus commodo viverra maecenas accumsan lacus vel facilisis. Sed ut perspiciatis unde omnis iste natus error sit voluptatem accusantium doloremque laudantium, totam rem aperiam, eaque ipsa quae ab illo inventore veritatis et quasi architecto beatae vitae dicta sunt explicabo. Nemo enim ipsam voluptatem quia voluptas sit aspernatur aut odit aut fugit, sed quia consequuntur magni dolores eos.</p>
      <div role="img" aria-label="Smiling girl stretching on a blue mat in a class" style="left:8px;top:119px;width:80px;height:48px;background:linear-gradient(135deg,#6a8fd0,#d9b8a8 50%,#3a6ab8)"></div>
      <h2 style="left:8px;top:175px;width:80px;font-size:4px;line-height:4.8px;color:var(--ink)">Lorem ipsum dolor sit ametlol cons ectetur adipiscing elitlorem.</h2>
      <p class="p" style="left:8px;top:187px;width:80px;font-size:1.8px;line-height:2.4px">Lorem ipsum dolor sit amet, consectetur adipiscing elit, sed do eiusmod tempor incididunt ut labore et dolore magna aliqua. Quis ipsum suspendisse ultrices gravida. Sed ut perspiciatis unde omnis iste natus error sit voluptatem accusantium doloremque laudantium, totam rem aperiam, eaque ipsa quae ab illo inventore veritatis. Nemo enim ipsam voluptatem quia voluptas sit aspernatur aut odit.</p>
      <p class="p" style="left:8px;top:223px;font-size:2.2px;color:#333">Share Article:</p>
      <i style="left:28px;top:222px;width:5px;height:5px;border-radius:50%;background:#2a5ac8"></i>
      <i style="left:35px;top:222px;width:5px;height:5px;border-radius:50%;background:#2aa0e8"></i>
      <i style="left:42px;top:222px;width:5px;height:5px;border-radius:50%;background:#e03a4a"></i>
      <i style="left:49px;top:222px;width:5px;height:5px;border-radius:50%;background:#2ab85a"></i>
    </article>
    <section class="card" style="left:13px;top:349px;width:94px;height:81px">
      <h3 style="left:8px;top:9px;font-size:2.6px;color:var(--ink)">Leave a Reply</h3>
      <i style="left:8px;top:13px;width:80px;height:.4px;background:var(--teal)"></i>
      <div class="field" style="left:8px;top:16px;width:80px;height:21px">Comment</div>
      <div class="field" style="left:8px;top:40px;width:40px;height:5px">Name</div>
      <div class="field" style="left:48px;top:40px;width:40px;height:5px">Email</div>
      <div class="field" style="left:8px;top:49px;width:80px;height:5px">Website</div>
      <p class="p" style="left:8px;top:57px;font-size:1.6px">☐ Save my name, email, and website in this browser for the next time I comment.</p>
      <span class="btn" style="left:8px;top:64px;background:linear-gradient(90deg,#7a4fc0,#22b8d2)">Post Comment</span>
    </section>
    <h4 class="side-title" style="left:112px;top:104px">Recent Posts</h4>
    <div class="side-item" style="left:113px;top:116px"><i></i><b>Lorem ipsum dolor sit amet, consectetur loremalilist<em>August 11, 2023</em></b></div>
    <div class="side-item" style="left:113px;top:132px"><i></i><b>Lorem ipsum dolor sit amet, consectetur loremalilist<em>August 11, 2023</em></b></div>
    <div class="side-item" style="left:113px;top:149px"><i></i><b>Lorem ipsum dolor sit amet, consectetur loremalilist<em>August 11, 2023</em></b></div>
    <div class="side-item" style="left:113px;top:165px"><i></i><b>Lorem ipsum dolor sit amet, consectetur loremalilist<em>August 11, 2023</em></b></div>
    <h4 class="side-title" style="left:113px;top:191px">Advertising</h4>
    <div role="img" aria-label="Advert photo of smiling children in a row" style="left:114px;top:203px;width:41px;height:37px;background:linear-gradient(135deg,#9ccbe8,#d9b0a0 50%,#6fa8d8)"></div>
    <div style="left:114px;top:240px;width:41px;height:20px;background:var(--purple);clip-path:polygon(0 15%,100% 0,100% 100%,0 100%)"></div>
    <p class="script" style="left:114px;top:246px;width:41px;text-align:center;white-space:normal;font-size:3px;line-height:3.2px;color:#fff">Lorem ipsum dolor sit amet consectetur adipiscing elit sed do eiusmod temp</p>
    <footer class="footer" style="top:449px;height:54px">
      <h4 class="foot-h" style="left:19px;top:8px">Contact Us</h4>
      <p class="foot-l" style="left:19px;top:17px">Contact: Dana Whitfield<br>Phone: 0400 118 236<br>Email: info@openharboryoga.com.au<br>Location: Lakeview, Victoria Australia 3999</p>
      <div class="foot-mark" style="top:9px"><i></i><span>OpenHarbor Yoga</span></div>
      <h4 class="foot-h" style="left:106px;top:8px">Connect With Us</h4>
      <p class="foot-l" style="left:106px;top:17px">Facebook: OpenHarbor Yoga<br>Instagram: openharboryogakids<br><br>ABN: 11 222 333 444</p>
      <p class="copy" style="top:46px">Copyright 2023 OpenHarbor Yoga</p>
    </footer>
  </section>

  <!-- CONTACT -->
  <section class="page" style="left:592px;top:726px;height:246px">
    <div class="topbar"><span>info@openharboryoga.com.au</span><b>Call Us: 0400 118 236</b></div>
    <nav class="navbar"><div class="nav-brand"><i></i></div>
      <div class="menu"><span>Home</span><span>About</span><span>Classes</span><span>Blog</span><span class="on">Contact</span></div>
      <span class="pill">Enquire Now</span></nav>
    <header class="hero"><i class="hero-mark"></i><span class="hero-name">OpenHarbor Yoga</span></header>
    <form class="card" style="left:34px;top:99px;width:105px;height:80px">
      <h2 class="script" style="left:0;width:105px;text-align:center;top:5px;font-size:8px">Contact</h2>
      <div class="field" style="left:12px;top:22px;width:44px;height:5px">Name</div>
      <div class="field" style="left:56px;top:22px;width:37px;height:5px">Email</div>
      <div class="field" style="left:12px;top:30px;width:81px;height:5px">Phone</div>
      <div class="field" style="left:12px;top:38px;width:81px;height:20px">Message</div>
      <p class="p" style="left:12px;top:61px;font-size:1.8px;color:var(--purple)">☐ Subscribe to Newsletter</p>
      <span class="btn" style="left:43px;top:67px;background:linear-gradient(90deg,#7a4fc0,#22b8d2)">Submit Now</span>
    </form>
    <footer class="footer" style="top:188px;height:58px">
      <h4 class="foot-h" style="left:19px;top:10px">Contact Us</h4>
      <p class="foot-l" style="left:19px;top:19px">Contact: Dana Whitfield<br>Phone: 0400 118 236<br>Email: info@openharboryoga.com.au<br>Location: Lakeview, Victoria Australia 3999</p>
      <div class="foot-mark"><i></i><span>OpenHarbor Yoga</span></div>
      <h4 class="foot-h" style="left:106px;top:10px">Connect With Us</h4>
      <p class="foot-l" style="left:106px;top:19px">Facebook: OpenHarbor Yoga<br>Instagram: openharboryogakids<br><br>ABN: 11 222 333 444</p>
      <p class="copy" style="top:50px">Copyright 2023 OpenHarbor Yoga</p>
    </footer>
  </section>

  <!-- ABOUT -->
  <section class="page" style="left:170px;top:791px;height:287px">
    <div class="topbar"><span>info@openharboryoga.com.au</span><b>Call Us: 0400 118 236</b></div>
    <nav class="navbar"><div class="nav-brand"><i></i></div>
      <div class="menu"><span>Home</span><span class="on">About</span><span>Classes</span><span>Blog</span><span>Contact</span></div>
      <span class="pill">Enquire Now</span></nav>
    <header class="hero"><i class="hero-mark"></i><span class="hero-name">OpenHarbor Yoga</span></header>
    <h2 class="script" style="left:0;width:172px;text-align:center;top:98px;font-size:9px">Hi and welcome to OpenHarbor Yoga!</h2>
    <p class="script" style="left:0;width:172px;text-align:center;top:111px;font-size:4.5px;line-height:4.6px;color:var(--purple)">My name is Dana, and I am the founder<br>&amp; facilitator of OpenHarbor Yoga</p>
    <p class="p c" style="left:28px;top:122px;width:116px">With the increasing numbers of youth mental health, I have started OpenHarbor Yoga wanting to assist children and teens with their mental health for life, with the magic of yoga.<br><br>I had always wanted to teach children, but had never found the right platform to do so... That was until I found yoga!<br><br>I genuinely believe the practice of yoga and mindfulness especially at a young age can offer life-long tools to kids and teens such as dealing with their emotions, developing resilience, self-awareness, respect and confidence in a fun environment.<br><br>I decided to combine my passion for mental health, wanting to make a difference in today's youth, with giving back to the community and my love for yoga. This led to me completing my teacher's training in children's yoga through a local yoga school.<br><br>I am proud and excited to have created OpenHarbor Yoga, and I love to share my knowledge of yoga with family and friends and now with kids and teens so that they have the tools they need to feel calm, courageous and compassionate.</p>
    <h3 class="script" style="left:0;width:172px;text-align:center;top:196px;font-size:5.5px;color:var(--purple)">Heartfelt Intention...</h3>
    <p class="p c" style="left:36px;top:207px;width:100px">OpenHarbor Yoga's vision is to influence our youth's mental health and wellbeing, so they grow into happy and balanced adults who impact their world with positivity.</p>
    <footer class="footer" style="top:229px;height:58px">
      <h4 class="foot-h" style="left:19px;top:10px">Contact Us</h4>
      <p class="foot-l" style="left:19px;top:19px">Contact: Dana Whitfield<br>Phone: 0400 118 236<br>Email: info@openharboryoga.com.au<br>Location: Lakeview, Victoria Australia 3999</p>
      <div class="foot-mark"><i></i><span>OpenHarbor Yoga</span></div>
      <h4 class="foot-h" style="left:106px;top:10px">Connect With Us</h4>
      <p class="foot-l" style="left:106px;top:19px">Facebook: OpenHarbor Yoga<br>Instagram: openharboryogakids<br><br>ABN: 11 222 333 444</p>
      <p class="copy" style="top:50px">Copyright 2023 OpenHarbor Yoga</p>
    </footer>
  </section>

</main>
</body>
</html>
```